Step and Repeat Backdrop for wedding reception photo booth

Would like to have a Step and Repeat Backdrop (8 foot high by 10 foot wide) that incorporates the wedding logo (attached) and the names Helen and Gavin. Background should be white, and wedding colors are burgundy and gold. Show me creativity :-) I have included some random samples.

```html
<!DOCTYPE html>
<html lang="en">
<head>
<meta charset="utf-8">
<title>Helen &amp; Gavin – Step and Repeat Backdrop</title>
<link rel="stylesheet" href="https://fonts.googleapis.com/css2?family=Playfair+Display:wght@500&family=Cormorant+Garamond:wght@600&display=swap">
<style>
  :root {
    --page: #ffffff;
    --burgundy: #8c1434;
    --gold-dark: #d4951f;
    --gold: #f2c531;
    --gold-light: #f7e68a;
    --gold-grad: linear-gradient(90deg, var(--gold-dark) 0%, var(--gold) 45%, var(--gold-light) 100%);
  }
  * { margin: 0; padding: 0; box-sizing: border-box; }
  html, body { width: 1200px; height: 1200px; overflow: hidden; background: var(--page); }

  .backdrop {
    position: absolute; left: 50px; top: 151px;
    width: 1100px; height: 898px;
    background: var(--burgundy);
    overflow: hidden;
  }

  .repeat-grid {
    position: absolute; inset: 0;
    display: grid;
    grid-template-columns: repeat(8, 1fr);
    grid-template-rows: repeat(8, 1fr);
    padding: 22px 1px 20px 1px;
  }
  .tile {
    display: flex; flex-direction: column; align-items: center; justify-content: center;
    gap: 3px;
  }
  .tile--hidden { visibility: hidden; }
  .tile__ornament {
    width: 84px; height: 11px;
    background: var(--gold-grad);
    opacity: .6;
    border-radius: 50%;
  }
  .tile__monogram {
    font-family: "Playfair Display", serif;
    font-weight: 500;
    font-size: 30px; line-height: 36px;
    color: var(--gold);
    letter-spacing: -1px;
  }

  .emblem {
    position: absolute; left: 261px; top: 157px;
    width: 580px; height: 580px;
  }
  .emblem__frame { position: absolute; inset: 0; }
  .emblem__flourish {
    position: absolute; left: 150px; width: 280px; height: 36px;
    background: var(--gold-grad);
    opacity: .55;
    border-radius: 50%;
  }
  .emblem__flourish--top { top: 128px; }
  .emblem__flourish--bottom { top: 358px; }
  .emblem__monogram {
    position: absolute; left: 0; right: 0; top: 180px;
    text-align: center;
    font-family: "Playfair Display", serif;
    font-weight: 500;
    font-size: 150px; line-height: 160px;
    letter-spacing: -6px;
    background: var(--gold-grad);
    -webkit-background-clip: text; background-clip: text;
    color: transparent;
  }
  .emblem__spray {
    position: absolute; top: 330px; width: 78px; height: 170px;
    background: linear-gradient(180deg, var(--gold-light) 0%, var(--gold) 40%, var(--gold-dark) 100%);
    opacity: .45;
    border-radius: 50% 50% 45% 45% / 60% 60% 40% 40%;
    z-index: 0;
  }
  .emblem__spray--left { left: 48px; transform: rotate(-18deg); }
  .emblem__spray--right { left: 454px; transform: rotate(18deg); }

  .name-banner {
    position: absolute; left: 107px; top: 446px;
    width: 363px; height: 64px;
    z-index: 1;
    background: linear-gradient(90deg, var(--gold-dark), var(--gold) 50%, var(--gold-light));
    clip-path: polygon(0 0, 100% 0, 98% 100%, 2% 100%);
    display: flex; align-items: center; justify-content: center; gap: 10px;
    font-family: "Cormorant Garamond", serif;
    font-weight: 600;
    font-size: 22px;
    letter-spacing: 9px;
    color: var(--burgundy);
    padding-top: 8px;
  }
  .name-banner__rings { width: 28px; height: 22px; }
</style>
</head>
<body>
<main class="backdrop">
  <section class="repeat-grid">
    <!-- row 1 -->
    <div class="tile"><span class="tile__ornament" role="img" aria-label="Gold flourish"></span><span class="tile__monogram">H&amp;G</span><span class="tile__ornament" role="img" aria-label="Gold flourish"></span></div>
    <div class="tile"><span class="tile__ornament" role="img" aria-label="Gold flourish"></span><span class="tile__monogram">H&amp;G</span><span class="tile__ornament" role="img" aria-label="Gold flourish"></span></div>
    <div class="tile"><span class="tile__ornament" role="img" aria-label="Gold flourish"></span><span class="tile__monogram">H&amp;G</span><span class="tile__ornament" role="img" aria-label="Gold flourish"></span></div>
    <div class="tile"><span class="tile__ornament" role="img" aria-label="Gold flourish"></span><span class="tile__monogram">H&amp;G</span><span class="tile__ornament" role="img" aria-label="Gold flourish"></span></div>
    <div class="tile"><span class="tile__ornament" role="img" aria-label="Gold flourish"></span><span class="tile__monogram">H&amp;G</span><span class="tile__ornament" role="img" aria-label="Gold flourish"></span></div>
    <div class="tile"><span class="tile__ornament" role="img" aria-label="Gold flourish"></span><span class="tile__monogram">H&amp;G</span><span class="tile__ornament" role="img" aria-label="Gold flourish"></span></div>
    <div class="tile"><span class="tile__ornament" role="img" aria-label="Gold flourish"></span><span class="tile__monogram">H&amp;G</span><span class="tile__ornament" role="img" aria-label="Gold flourish"></span></div>
    <div class="tile"><span class="tile__ornament" role="img" aria-label="Gold flourish"></span><span class="tile__monogram">H&amp;G</span><span class="tile__ornament" role="img" aria-label="Gold flourish"></span></div>
    <!-- row 2 -->
    <div class="tile"><span class="tile__ornament" role="img" aria-label="Gold flourish"></span><span class="tile__monogram">H&amp;G</span><span class="tile__ornament" role="img" aria-label="Gold flourish"></span></div>
    <div class="tile"><span class="tile__ornament" role="img" aria-label="Gold flourish"></span><span class="tile__monogram">H&amp;G</span><span class="tile__ornament" role="img" aria-label="Gold flourish"></span></div>
    <div class="tile"><span class="tile__ornament" role="img" aria-label="Gold flourish"></span><span class="tile__monogram">H&amp;G</span><span class="tile__ornament" role="img" aria-label="Gold flourish"></span></div>
    <div class="tile tile--hidden"></div>
    <div class="tile tile--hidden"></div>
    <div class="tile"><span class="tile__ornament" role="img" aria-label="Gold flourish"></span><span class="tile__monogram">H&amp;G</span><span class="tile__ornament" role="img" aria-label="Gold flourish"></span></div>
    <div class="tile"><span class="tile__ornament" role="img" aria-label="Gold flourish"></span><span class="tile__monogram">H&amp;G</span><span class="tile__ornament" role="img" aria-label="Gold flourish"></span></div>
    <div class="tile"><span class="tile__ornament" role="img" aria-label="Gold flourish"></span><span class="tile__monogram">H&amp;G</span><span class="tile__ornament" role="img" aria-label="Gold flourish"></span></div>
    <!-- rows 3-6 -->
    <div class="tile"><span class="tile__ornament" role="img" aria-label="Gold flourish"></span><span class="tile__monogram">H&amp;G</span><span class="tile__ornament" role="img" aria-label="Gold flourish"></span></div>
    <div class="tile"><span class="tile__ornament" role="img" aria-label="Gold flourish"></span><span class="tile__monogram">H&amp;G</span><span class="tile__ornament" role="img" aria-label="Gold flourish"></span></div>
    <div class="tile tile--hidden"></div><div class="tile tile--hidden"></div><div class="tile tile--hidden"></div><div class="tile tile--hidden"></div>
    <div class="tile"><span class="tile__ornament" role="img" aria-label="Gold flourish"></span><span class="tile__monogram">H&amp;G</span><span class="tile__ornament" role="img" aria-label="Gold flourish"></span></div>
    <div class="tile"><span class="tile__ornament" role="img" aria-label="Gold flourish"></span><span class="tile__monogram">H&amp;G</span><span class="tile__ornament" role="img" aria-label="Gold flourish"></span></div>

    <div class="tile"><span class="tile__ornament" role="img" aria-label="Gold flourish"></span><span class="tile__monogram">H&amp;G</span><span class="tile__ornament" role="img" aria-label="Gold flourish"></span></div>
    <div class="tile"><span class="tile__ornament" role="img" aria-label="Gold flourish"></span><span class="tile__monogram">H&amp;G</span><span class="tile__ornament" role="img" aria-label="Gold flourish"></span></div>
    <div class="tile tile--hidden"></div><div class="tile tile--hidden"></div><div class="tile tile--hidden"></div><div class="tile tile--hidden"></div>
    <div class="tile"><span class="tile__ornament" role="img" aria-label="Gold flourish"></span><span class="tile__monogram">H&amp;G</span><span class="tile__ornament" role="img" aria-label="Gold flourish"></span></div>
    <div class="tile"><span class="tile__ornament" role="img" aria-label="Gold flourish"></span><span class="tile__monogram">H&amp;G</span><span class="tile__ornament" role="img" aria-label="Gold flourish"></span></div>

    <div class="tile"><span class="tile__ornament" role="img" aria-label="Gold flourish"></span><span class="tile__monogram">H&amp;G</span><span class="tile__ornament" role="img" aria-label="Gold flourish"></span></div>
    <div class="tile"><span class="tile__ornament" role="img" aria-label="Gold flourish"></span><span class="tile__monogram">H&amp;G</span><span class="tile__ornament" role="img" aria-label="Gold flourish"></span></div>
    <div class="tile tile--hidden"></div><div class="tile tile--hidden"></div><div class="tile tile--hidden"></div><div class="tile tile--hidden"></div>
    <div class="tile"><span class="tile__ornament" role="img" aria-label="Gold flourish"></span><span class="tile__monogram">H&amp;G</span><span class="tile__ornament" role="img" aria-label="Gold flourish"></span></div>
    <div class="tile"><span class="tile__ornament" role="img" aria-label="Gold flourish"></span><span class="tile__monogram">H&amp;G</span><span class="tile__ornament" role="img" aria-label="Gold flourish"></span></div>

    <div class="tile"><span class="tile__ornament" role="img" aria-label="Gold flourish"></span><span class="tile__monogram">H&amp;G</span><span class="tile__ornament" role="img" aria-label="Gold flourish"></span></div>
    <div class="tile"><span class="tile__ornament" role="img" aria-label="Gold flourish"></span><span class="tile__monogram">H&amp;G</span><span class="tile__ornament" role="img" aria-label="Gold flourish"></span></div>
    <div class="tile tile--hidden"></div><div class="tile tile--hidden"></div><div class="tile tile--hidden"></div><div class="tile tile--hidden"></div>
    <div class="tile"><span class="tile__ornament" role="img" aria-label="Gold flourish"></span><span class="tile__monogram">H&amp;G</span><span class="tile__ornament" role="img" aria-label="Gold flourish"></span></div>
    <div class="tile"><span class="tile__ornament" role="img" aria-label="Gold flourish"></span><span class="tile__monogram">H&amp;G</span><span class="tile__ornament" role="img" aria-label="Gold flourish"></span></div>
    <!-- row 7 -->
    <div class="tile"><span class="tile__ornament" role="img" aria-label="Gold flourish"></span><span class="tile__monogram">H&amp;G</span><span class="tile__ornament" role="img" aria-label="Gold flourish"></span></div>
    <div class="tile"><span class="tile__ornament" role="img" aria-label="Gold flourish"></span><span class="tile__monogram">H&amp;G</span><span class="tile__ornament" role="img" aria-label="Gold flourish"></span></div>
    <div class="tile tile--hidden"></div>
    <div class="tile tile--hidden"></div>
    <div class="tile tile--hidden"></div>
    <div class="tile tile--hidden"></div>
    <div class="tile"><span class="tile__ornament" role="img" aria-label="Gold flourish"></span><span class="tile__monogram">H&amp;G</span><span class="tile__ornament" role="img" aria-label="Gold flourish"></span></div>
    <div class="tile"><span class="tile__ornament" role="img" aria-label="Gold flourish"></span><span class="tile__monogram">H&amp;G</span><span class="tile__ornament" role="img" aria-label="Gold flourish"></span></div>
    <!-- row 8 -->
    <div class="tile"><span class="tile__ornament" role="img" aria-label="Gold flourish"></span><span class="tile__monogram">H&amp;G</span><span class="tile__ornament" role="img" aria-label="Gold flourish"></span></div>
    <div class="tile"><span class="tile__ornament" role="img" aria-label="Gold flourish"></span><span class="tile__monogram">H&amp;G</span><span class="tile__ornament" role="img" aria-label="Gold flourish"></span></div>
    <div class="tile"><span class="tile__ornament" role="img" aria-label="Gold flourish"></span><span class="tile__monogram">H&amp;G</span><span class="tile__ornament" role="img" aria-label="Gold flourish"></span></div>
    <div class="tile"><span class="tile__ornament" role="img" aria-label="Gold flourish"></span><span class="tile__monogram">H&amp;G</span><span class="tile__ornament" role="img" aria-label="Gold flourish"></span></div>
    <div class="tile"><span class="tile__ornament" role="img" aria-label="Gold flourish"></span><span class="tile__monogram">H&amp;G</span><span class="tile__ornament" role="img" aria-label="Gold flourish"></span></div>
    <div class="tile"><span class="tile__ornament" role="img" aria-label="Gold flourish"></span><span class="tile__monogram">H&amp;G</span><span class="tile__ornament" role="img" aria-label="Gold flourish"></span></div>
    <div class="tile"><span class="tile__ornament" role="img" aria-label="Gold flourish"></span><span class="tile__monogram">H&amp;G</span><span class="tile__ornament" role="img" aria-label="Gold flourish"></span></div>
    <div class="tile"><span class="tile__ornament" role="img" aria-label="Gold flourish"></span><span class="tile__monogram">H&amp;G</span><span class="tile__ornament" role="img" aria-label="Gold flourish"></span></div>
  </section>

  <section class="emblem">
    <svg class="emblem__frame" viewBox="0 0 580 580" width="580" height="580" aria-hidden="true">
      <defs>
        <linearGradient id="goldStroke" x1="0" y1="0" x2="1" y2="0">
          <stop offset="0" stop-color="#d4951f"/>
          <stop offset=".45" stop-color="#f2c531"/>
          <stop offset="1" stop-color="#f7e68a"/>
        </linearGradient>
      </defs>
      <polygon points="283,4 400,30 540,170 540,290 560,300 500,460 290,570 165,540 40,460 10,280 35,160 90,85"
               fill="none" stroke="url(#goldStroke)" stroke-width="7" stroke-linejoin="miter"/>
      <polygon points="130,120 290,30 400,40 530,180 548,320 520,460 400,515 185,552 55,465 35,270 48,230"
               fill="none" stroke="url(#goldStroke)" stroke-width="2.5"/>
    </svg>
    <div class="emblem__flourish emblem__flourish--top" role="img" aria-label="Gold scroll flourish with fleur-de-lis"></div>
    <div class="emblem__monogram">H&amp;G</div>
    <div class="emblem__flourish emblem__flourish--bottom" role="img" aria-label="Gold scroll flourish with fleur-de-lis"></div>
    <div class="emblem__spray emblem__spray--left" role="img" aria-label="Gold floral spray"></div>
    <div class="emblem__spray emblem__spray--right" role="img" aria-label="Gold floral spray"></div>
    <div class="name-banner">
      <span class="name-banner__name">Helen</span>
      <svg class="name-banner__rings" viewBox="0 0 28 22" aria-hidden="true">
        <circle cx="10" cy="12" r="7.5" fill="none" stroke="#8c1434" stroke-width="2"/>
        <circle cx="18" cy="12" r="7.5" fill="none" stroke="#8c1434" stroke-width="2"/>
      </svg>
      <span class="name-banner__name">Gavin</span>
    </div>
  </section>
</main>
</body>
</html>
```